Business Cards for new orthopaedic surgery practice

My husband and I are starting our own orthopaedic surgery practice. We are looking for a business card that is uniform, but one will have my name/title and the other will have his. You can just create one design with my name on it for now. But when I choose your design as the winning design I will ask that you add another copy with his name/title.

We are looking for classy, simple, elite all in one. We like dark blues/a little gold/yellow. Something that goes with our logo. We want our logo incorporated. Here is all the info you need:
Business name: RV Bone & Vitality Center
Location: 38517 North Willowmere Ave
Maple Hollow, FL 33190
Phone: 954-218-4063
Fax: 954-582-7341
Email: info@myrvbonecare.example

Names: Lydia Vance, M.D.
Board Certified Hand and Upper Extremity Surgeon

Ebo Dansu, M.D.
Board Certified Hip & Knee Replacement/General Orthopaedic Surgeon

Can decide what you want to put on the back. Maybe a slogan:
Steady Hands. Lasting Strength

I am just going to upload our logo. The only thing is if we select you as the winning design, the location, and phone numbers may change. We will need your help to update that once fully solidified.

Industry/Entity Type

Medical

Contact Information for Business Card

Colors
0054AA
0677BA
7BADD7
CADEEF
E8F1F8
0094D4
00A9DD
6FCCEA
C7EBF8
E9F6FB

Requirements
Must have
• class, appeal,
Should not have
• We want to air on the side of masculine if we are looking at masculine vs. feminine feel. But we still want it classy, sophisticated, and something we will love

```html
<!DOCTYPE html>
<html lang="en">
<head>
<meta charset="utf-8">
<title>RV Bone &amp; Vitality Center — Business Card</title>
<link rel="stylesheet" href="https://fonts.googleapis.com/css2?family=Tinos:wght@400;700&display=swap">
<style>
  :root {
    --navy: #1a2a55;
    --navy-deep: #15224a;
    --navy-soft: #2c3f78;
    --gold: #c39a4a;
    --paper: #f7f7f6;
    --ink-grey: #6f6f6f;
    --backdrop: #e6e6e4;
  }
  * { box-sizing: border-box; margin: 0; padding: 0; }
  html, body { width: 1200px; height: 801px; overflow: hidden; }
  body {
    background: var(--backdrop);
    font-family: "Tinos", "Times New Roman", serif;
    display: flex;
    align-items: center;
    justify-content: center;
    gap: 40px;
  }
  .card {
    position: relative;
    width: 540px;
    height: 309px;
    border-bottom: 4px solid var(--gold);
    border-right: 2px solid var(--gold);
    box-shadow: 0 8px 22px rgba(0,0,0,.18);
    overflow: hidden;
  }

  /* Front */
  .card--front { background: var(--paper); }
  .brand {
    position: absolute;
    display: flex;
    align-items: center;
    gap: 10px;
    color: var(--navy);
    font-weight: 700;
    letter-spacing: .08em;
    text-transform: uppercase;
  }
  .brand__dot {
    flex: none;
    border: 2px solid var(--gold);
    border-radius: 50%;
  }
  .card--front .brand { top: 30px; right: 28px; width: 200px; font-size: 15px; line-height: 1.35; }
  .card--front .brand__dot { width: 34px; height: 34px; }
  .person { position: absolute; left: 34px; top: 92px; }
  .person__name { font-size: 24px; font-weight: 700; color: var(--navy); }
  .person__title { font-size: 16px; color: var(--ink-grey); line-height: 1.2; margin-top: 2px; }
  .rule {
    position: absolute;
    left: 34px; right: 28px; top: 172px;
    height: 1.5px;
    background: var(--gold);
  }
  .contacts { position: absolute; left: 34px; top: 188px; list-style: none; }
  .contacts li {
    display: flex; align-items: center; gap: 8px;
    font-size: 16px; color: var(--ink-grey); line-height: 1.45;
  }
  .contacts svg { width: 13px; height: 13px; fill: var(--gold); flex: none; }
  .address {
    position: absolute; right: 28px; top: 188px;
    font-style: normal; text-align: right;
    font-size: 16px; color: var(--ink-grey); line-height: 1.45;
  }

  /* Back */
  .card--back {
    background: linear-gradient(135deg, var(--navy-deep), var(--navy));
  }
  .backdrop-name {
    position: absolute; left: 26px; bottom: 24px;
    font-size: 36px; font-weight: 700; line-height: 1.05;
    color: var(--navy-soft);
    letter-spacing: .04em;
    text-transform: uppercase;
  }
  .card--back .brand { top: 48px; right: 34px; width: 220px; font-size: 17px; line-height: 1.35; color: #fff; }
  .card--back .brand__dot { width: 40px; height: 40px; }
  .slogan {
    position: absolute; right: 30px; bottom: 56px;
    font-size: 17px; font-weight: 700; color: var(--gold);
  }
</style>
</head>
<body>

<section class="card card--front" aria-label="Business card front">
  <div class="brand"><span class="brand__dot"></span><span>RV Bone &amp; Vitality Center</span></div>
  <div class="person">
    <p class="person__name">Lydia Vance, M.D.</p>
    <p class="person__title">Board Certified Hand and<br>Upper Extremity Surgeon</p>
  </div>
  <div class="rule"></div>
  <ul class="contacts">
    <li><svg viewBox="0 0 16 16" aria-hidden="true"><path d="M3.5 1.5l2.5 3-1.5 1.5c.8 2 2.5 3.7 4.5 4.5L10.5 9l3 2.5-1.5 3C7 14 2 9 1.5 3z"/></svg>954-218-4063</li>
    <li><svg viewBox="0 0 16 16" aria-hidden="true"><path d="M4 1h8v4H4zM1 6h14v6h-3v3H4v-3H1zm4 4v4h6v-4z"/></svg>954-582-7341</li>
    <li><svg viewBox="0 0 16 16" aria-hidden="true"><path d="M1 3h14v10H1zm1.5 1.5L8 9l5.5-4.5z"/></svg>info@myrvbonecare.example</li>
  </ul>
  <address class="address">38517 North Willowmere Ave<br>Maple Hollow, FL 33190</address>
</section>

<section class="card card--back" aria-label="Business card back">
  <div class="backdrop-name">RV Bone &amp;<br>Vitality</div>
  <div class="brand"><span class="brand__dot"></span><span>RV Bone &amp; Vitality Center</span></div>
  <p class="slogan">Steady Hands. Lasting Strength</p>
</section>

</body>
</html>
```